ORV Fashion Design Company Needs a New Web Design, Please Click Me

Designers:

PLEASE NOTE: we only need the web page design, not a fully coded website.

Our brand's name is Orbel Vantra, our signature is print. our style is edgy and chic.

The old website is too messy. here's the address:
www.orvdesign.example.cn

The new website's purpose is to show our brand/design and most importantly, sell products, So it should be a combination of a designer official website and online shopping. I want the whole style to be clean, edgy and pioneer, easy to understand. we need a sophisticated online shopping website.

The reference websites are:
liromapek.example.uk
www.qd-besu.example
talemkorv.example
misolvare.example
pardelunitram.example

Please beat their designs :)

Check out our lasted fashion show to get to know us more.

https://www.videohost.example/watch?v=ZkrpLmWnaYd&spfreload=10

The attachments are our Logo and some 2015 Look Book.
(Please let us know if you want to play with our print in this particular web design, we can send the source file.)
Updates

Designers, we really like the design of helenamardoux.example(we have attached a picture of the website) , Can we get a homepage like that? so the designs you submit will be 3 pages. The first one should be a page that only has Shop/Look. then the shop page, it should be nothing but our product which we will list the categories ourself. And the look page should contain all the info. such as news, about us and designers etc. Thank you all for your hard work, we really enjoyed the designs. Added Monday, November 03, 2014

Target Market(s)

Our target audiences are woman aged from 16-40 who like online shopping

Industry/Entity Type

Online Shopping

Number of Pages Required

3 page

Font styles to use
Serif
Sans Serif
Script

Requirements
Must have
• Designers,
• we really like the design of helenamardoux.example(we have attached a picture of the website) , Can we get a homepage like that? so the designs you submit will be 3 pages. The first one should be a page that only has Shop/Look. then the shop page, it should be nothing but our product which we will list the categories ourself. And the look page should contain all the info. such as news, about us and designers etc. Thank you all for your hard work, we really enjoyed the designs.

```html
<!DOCTYPE html>
<html lang="en">
<head>
<meta charset="utf-8">
<title>ORV Group</title>
<link href="https://fonts.googleapis.com/css2?family=Noto+Serif&family=Roboto:wght@400;500&family=Open+Sans:wght@400;800&display=swap" rel="stylesheet">
<style>
:root{
  --red:#b70d0d;
  --red-deep:#a90909;
  --accent:#ef4b4b;
  --dark:#3a3a3a;
  --ink:#222;
  --text:#333;
  --rule:#e4e4e4;
  --white:#fff;
}
*{margin:0;padding:0;box-sizing:border-box}
html,body{width:1200px;height:1100px;overflow:hidden;background:var(--white)}
body{position:relative;font-family:"Roboto",sans-serif;color:var(--text)}
.abs{position:absolute}

.hero-band{left:0;top:0;width:1200px;height:395px;background:radial-gradient(circle at 50% 40%,#c31212,var(--red-deep))}
.tile{position:absolute;width:187.5px;background:var(--white);padding:3px 10px 0 14px}
.tile.lower{padding-top:192px}
.tile h3{font-family:"Noto Serif",serif;font-weight:400;color:var(--accent);font-size:14px;line-height:16px;margin-bottom:15px}
.tile p{font-size:9.6px;line-height:15px;color:var(--ink);white-space:nowrap;padding-left:1px}
.more{font-family:"Noto Serif",serif;font-size:9.5px;line-height:12px;color:var(--ink);margin-top:15px;display:flex;align-items:center;gap:3px;white-space:nowrap}
.photo{position:absolute}

.side-head{left:225px;top:425px;width:177px;height:34px;background:var(--dark);color:var(--white);font-family:"Noto Serif",serif;font-size:13px;line-height:16px;padding:9px 13px}
.menu{left:225px;top:459px;width:177px;list-style:none}
.menu li{height:37.6px;border-bottom:1px solid var(--rule);font-size:11px;line-height:36px;color:var(--ink)}
.menu li::before{content:"▪";font-size:6px;margin-right:5px;vertical-align:2px}
.menu li.active{color:var(--accent)}
.promo{left:225px;top:743px;width:177px;height:144px;border-radius:4px;background:linear-gradient(110deg,#1d1d1d 55%,#6a4a3e);color:var(--white);font-family:"Open Sans",sans-serif;text-align:center}
.promo .big{position:absolute;left:0;right:0;top:16px;font-weight:800;font-size:33px;line-height:44px;letter-spacing:-1px}
.promo .sub{position:absolute;left:0;right:0;top:57px;font-size:14.5px;line-height:20px}
.promo .btn{position:absolute;left:36px;top:88px;width:105px;height:29px;background:#f22a10;font-size:12px;line-height:29px}

.welcome{left:741px;top:426px;width:240px}
.welcome h2{font-family:"Noto Serif",serif;font-weight:400;color:var(--accent);font-size:14px;line-height:16px;margin-bottom:15px}
.welcome p{font-size:9.6px;line-height:15px;color:var(--ink);white-space:nowrap}
.welcome .more{margin-top:19px}

.brand-title{left:417px;top:685px;font-family:"Noto Serif",serif;font-size:13px;line-height:16px;color:var(--ink)}
.stripe{left:562px;top:688px;width:413px;height:9px;background:repeating-linear-gradient(135deg,#d4d4d4 0 1px,transparent 1px 4px)}

.card{position:absolute;top:724px;width:176px;height:307px;border:1px solid var(--rule);text-align:center}
.card .pic{position:absolute;left:11px;top:12px;width:151px;height:172px;border:1px solid #ddd}
.card h4{position:absolute;left:0;right:0;top:200px;font-family:"Noto Serif",serif;font-weight:400;font-size:10.5px;line-height:14px;color:var(--ink)}
.card p{position:absolute;left:0;right:0;top:225px;font-size:9.6px;line-height:15px;color:var(--ink);white-space:nowrap}
.card .rule{position:absolute;left:0;right:0;top:266px;border-top:1px solid var(--rule)}
.card .btn{position:absolute;left:9px;top:272px;width:156px;height:28px;background:var(--red);color:var(--white);font-size:11px;letter-spacing:2.5px;line-height:28px}
.card .btn.dark{background:var(--dark)}

.foot-rule{left:0;top:1055px;width:1200px;border-top:1px solid var(--rule)}
.feature{top:1080px;display:flex;align-items:center;gap:8px;font-family:"Noto Serif",serif;font-size:13.5px;line-height:18px;color:var(--ink)}
</style>
</head>
<body>

<div class="abs hero-band"></div>

<div class="photo" role="img" aria-label="Model in white blouse and black skirt, dimmed with plus overlay" style="left:225px;top:0;width:188px;height:177px;background:linear-gradient(#5a5a5a,#3e3e3e)">
  <svg class="abs" style="left:78px;top:66px" width="32" height="32"><path d="M16 0V32M0 16H32" stroke="#fff" stroke-width="1.5"/></svg>
</div>
<div class="tile" style="left:413px;top:0;height:177px">
  <h3>LOREM IPSUM</h3>
  <p>Lorem Ipsum is simply dummy text of<br>the printing and typesetting industry.<br>Lorem Ipsum has been the industry's<br>standard dummy text ever.</p>
  <div class="more"><svg width="7" height="6"><path d="M0 3H6M3.5 .5 6 3 3.5 5.5" stroke="#222" fill="none"/></svg>VIEW MORE</div>
</div>
<div class="photo" role="img" aria-label="Model in white top, trousers and straw hat" style="left:600px;top:0;width:188px;height:177px;background:linear-gradient(#f0efec,#e2e0dc)"></div>
<div class="tile" style="left:788px;top:0;height:177px">
  <h3>LOREM IPSUM</h3>
  <p>Lorem Ipsum is simply dummy text of<br>the printing and typesetting industry.<br>Lorem Ipsum has been the industry's<br>standard dummy text ever.</p>
  <div class="more"><svg width="7" height="6"><path d="M0 3H6M3.5 .5 6 3 3.5 5.5" stroke="#222" fill="none"/></svg>VIEW MORE</div>
</div>

<div class="tile" style="left:225px;top:177px;height:187px;padding-top:16px;padding-left:9px">
  <h3>LOREM IPSUM</h3>
  <p>Lorem Ipsum is simply dummy text of<br>the printing and typesetting industry.<br>Lorem Ipsum has been the industry's<br>standard dummy text ever.</p>
  <div class="more"><svg width="7" height="6"><path d="M0 3H6M3.5 .5 6 3 3.5 5.5" stroke="#222" fill="none"/></svg>VIEW MORE</div>
</div>
<div class="photo" role="img" aria-label="Male model in dark printed shirt" style="left:413px;top:177px;width:187px;height:187px;background:radial-gradient(circle at 50% 60%,#5a4548,#d8d8d8 75%)"></div>
<div class="tile" style="left:600px;top:177px;height:187px;padding-top:16px;padding-left:15px">
  <h3>LOREM IPSUM</h3>
  <p>Lorem Ipsum is simply dummy text of<br>the printing and typesetting industry.<br>Lorem Ipsum has been the industry's<br>standard dummy text ever.</p>
  <div class="more"><svg width="7" height="6"><path d="M0 3H6M3.5 .5 6 3 3.5 5.5" stroke="#222" fill="none"/></svg>VIEW MORE</div>
</div>
<div class="photo" role="img" aria-label="Runway show with model on red carpet" style="left:788px;top:177px;width:187px;height:187px;background:linear-gradient(160deg,#2a1020,#7a0d1e 55%,#c0142a)"></div>

<div class="abs side-head">MAIN FEATURES</div>
<ul class="abs menu">
  <li>New products</li>
  <li class="active">Top sellers</li>
  <li>Specials</li>
  <li>Manufacturers</li>
  <li>Suppliers</li>
  <li>Specials</li>
  <li>Customer Service</li>
</ul>
<div class="abs promo">
  <div class="big">50% OFF</div>
  <div class="sub">VESTRA SUNGLASSES</div>
  <div class="btn">SHOP NOW!</div>
</div>

<div class="photo" role="img" aria-label="Model in white coat and full skirt in a pale archway" style="left:417px;top:425px;width:300px;height:225px;background:linear-gradient(120deg,#e2e8e4,#f4f6f4 50%,#d9e0dc)"></div>

<div class="abs welcome">
  <h2>WELCOME TO ORV GROUP</h2>
  <p>Lorem Ipsum is simply dummy text of the printing and<br>typesetting industry. Lorem Ipsum has been the industry's<br>standard dummy text ever since the 1500s, when an<br>unknown printer took a galley of type and scrambled it to<br>make a type specimen book. It has survived not only five<br>centuries, but also the leap into electronic typesetting,<br>remaining essentially unchanged. It was popularised in<br>the 1960s with the release of Letraset sheets containing<br>Lorem Ipsum passages, and more recently with desktop<br>publishing software like Aldus PageMaker including<br>versions of Lorem Ipsum.</p>
  <div class="more"><svg width="7" height="6"><path d="M0 3H6M3.5 .5 6 3 3.5 5.5" stroke="#222" fill="none"/></svg>VIEW MORE</div>
</div>

<div class="abs brand-title">POPULAR BRAND</div>
<div class="abs stripe"></div>

<div class="card" style="left:416px">
  <div class="pic" role="img" aria-label="Model in red and black printed dress" style="background:linear-gradient(#f2f0ef 20%,#9a3a28 50%,#5a2a22)"></div>
  <h4>CURABITUR TEMPUS VELIT</h4>
  <p>Curabitur tempus velit in leo<br>fermentum quis tincidunt lorem...</p>
  <div class="rule"></div>
  <div class="btn">VIEW MORE</div>
</div>
<div class="card" style="left:607px">
  <div class="pic" role="img" aria-label="Model in colourful abstract print dress" style="background:linear-gradient(#f2f0ef 20%,#8fb3c9 50%,#d9a24a 75%,#f0ede8)"></div>
  <h4>CURABITUR TEMPUS VELIT</h4>
  <p>Curabitur tempus velit in leo<br>fermentum quis tincidunt lorem...</p>
  <div class="rule"></div>
  <div class="btn dark">VIEW MORE</div>
</div>
<div class="card" style="left:798px">
  <div class="pic" role="img" aria-label="Model in grey top with fur sleeves" style="background:linear-gradient(#f2f0ef 20%,#a6a6a6 50%,#cfcfcf 80%,#efece6)"></div>
  <h4>CURABITUR TEMPUS VELIT</h4>
  <p>Curabitur tempus velit in leo<br>fermentum quis tincidunt lorem...</p>
  <div class="rule"></div>
  <div class="btn">VIEW MORE</div>
</div>

<div class="abs foot-rule"></div>
<div class="abs feature" style="left:225px">
  <svg width="24" height="20"><path d="M2 18 22 4M6 18H20" stroke="#c9a24a" stroke-width="2" fill="none"/></svg>ENJOY FREE SHIPPING
</div>
<div class="abs feature" style="left:480px">
  <svg width="24" height="20"><rect x="4" y="3" width="14" height="17" fill="none" stroke="#999"/><circle cx="8" cy="16" r="4" fill="none" stroke="#999"/></svg>ON TIME DELIVERY
</div>
<div class="abs feature" style="left:734px">
  <svg width="24" height="20"><path d="M1 12A11 9 0 0 1 23 12Z" fill="#c9a24a"/><path d="M12 12V19" stroke="#c9a24a" stroke-width="2"/></svg>BEST SERVICES
</div>

</body>
</html>
```